Geschäftspapiere für Kindergarten
Zielgruppe
Es ist ein Kindergarten und Zielgruppe Kinder und Eltern. Wir suchen ein hochwertiges Design.
Aufgabenstellung
Es soll elegant und doch bunt und kreativ aussehen.

```html
<!DOCTYPE html>
<html lang="de">
<head>
<meta charset="utf-8">
<title>Keimlinge – Visitenkarte</title>
<link rel="stylesheet" href="https://fonts.googleapis.com/css2?family=Quicksand:wght@400;500;700&family=Patrick+Hand&family=Roboto:wght@300;400;700&display=swap">
<style>
  :root {
    --page: #e4e4e4;
    --card: #ffffff;
    --brand: #e8891c;
    --web-blue: #5b7fc8;
    --tag-green: #2f9a3c;
    --lime: #8cbc1e;
    --grey-text: #6f6f6f;
    --dark-text: #555555;
  }
  * { box-sizing: border-box; margin: 0; padding: 0; }
  html, body { width: 1200px; height: 842px; overflow: hidden; }
  body {
    background: var(--page);
    font-family: "Quicksand", sans-serif;
    position: relative;
  }
  .card {
    position: absolute;
    top: 253px;
    width: 520px;
    height: 336px;
    background: var(--card);
    overflow: hidden;
    box-shadow: 0 6px 18px rgba(0,0,0,.12);
  }
  .card--front { left: 50px; }
  .card--back { left: 630px; }

  .watercolor {
    position: absolute; inset: 0;
    background:
      radial-gradient(ellipse 45% 60% at 18% 55%, rgba(120,200,235,.75), transparent 70%),
      radial-gradient(ellipse 50% 70% at 50% 50%, rgba(255,226,110,.85), transparent 72%),
      radial-gradient(ellipse 35% 55% at 85% 60%, rgba(244,150,190,.7), transparent 70%),
      radial-gradient(ellipse 30% 40% at 65% 25%, rgba(255,236,150,.7), transparent 70%);
  }
  .watercolor--soft {
    background:
      radial-gradient(ellipse 30% 35% at 20% 40%, rgba(200,190,235,.4), transparent 70%),
      radial-gradient(ellipse 55% 55% at 45% 30%, rgba(255,240,170,.55), transparent 72%),
      radial-gradient(ellipse 30% 40% at 88% 55%, rgba(230,200,240,.45), transparent 70%);
  }

  .brand {
    position: absolute;
    display: flex; align-items: center; gap: 14px;
    color: var(--brand);
    font-weight: 500;
    letter-spacing: .08em;
    white-space: nowrap;
  }
  .brand__dot { border-radius: 50%; background: var(--brand); flex: none; }

  .card--front .brand { left: 0; right: 0; top: 120px; justify-content: center; font-size: 54px; }
  .card--front .brand__dot { width: 38px; height: 38px; }
  .web {
    position: absolute; left: 0; right: 0; top: 215px;
    text-align: center;
    font-family: "Roboto", sans-serif;
    font-size: 24px; color: var(--web-blue);
  }

  .card--back .brand { left: 36px; top: 36px; font-size: 40px; }
  .card--back .brand__dot { width: 60px; height: 60px; }
  .tagline {
    position: absolute; left: 112px; top: 86px;
    font-family: "Patrick Hand", cursive;
    font-size: 26px; color: var(--tag-green);
    white-space: nowrap;
  }
  .person {
    position: absolute; right: 40px; top: 132px;
    text-align: right;
    font-family: "Roboto", sans-serif;
  }
  .person__name { font-size: 28px; color: var(--grey-text); font-weight: 300; line-height: 1.1; }
  .person__name strong { color: var(--lime); font-weight: 700; }
  .person__role { font-size: 11px; letter-spacing: .06em; color: var(--dark-text); font-weight: 700; margin-top: 4px; }

  .contact {
    position: absolute; left: 40px; top: 180px;
    font-family: "Roboto", sans-serif;
    font-size: 14px; color: var(--dark-text);
    list-style: none;
  }
  .contact li { display: flex; align-items: flex-start; gap: 10px; margin-bottom: 8px; line-height: 1.25; }
  .contact svg { width: 14px; height: 14px; flex: none; margin-top: 2px; fill: var(--lime); }

  .accent-band {
    position: absolute; right: 0; bottom: 0;
    width: 260px; height: 120px;
    background: linear-gradient(160deg, transparent 35%, rgba(242,212,58,.35) 55%, rgba(140,188,30,.35) 70%, rgba(228,35,125,.25) 85%, transparent 100%);
  }
</style>
</head>
<body>

<section class="card card--front">
  <div class="watercolor" role="img" aria-label="Aquarellfläche in Hellblau, Gelb und Rosa"></div>
  <div class="brand"><span class="brand__dot"></span>KEIMLINGE</div>
  <p class="web">www.keimlinge-kita.de</p>
</section>

<section class="card card--back">
  <div class="watercolor watercolor--soft" role="img" aria-label="zarte Aquarellfläche in Pastelltönen"></div>
  <div class="accent-band" role="img" aria-label="geschwungenes Farbband in Gelb, Grün und Pink"></div>

  <div class="brand"><span class="brand__dot"></span>KEIMLINGE</div>
  <p class="tagline">Kinderhaus am Lindenhof</p>

  <div class="person">
    <p class="person__name">LENA <strong>VOGT</strong></p>
    <p class="person__role">CREATIVE DIRECTOR</p>
  </div>

  <ul class="contact">
    <li>
      <svg viewBox="0 0 16 16"><path d="M15 1 1 7l6 2 2 6z"/></svg>
      <span>Lindenweg 7<br>12345 Sonnstadt</span>
    </li>
    <li>
      <svg viewBox="0 0 16 16"><path d="M3 1h3l1 4-2 1a9 9 0 0 0 5 5l1-2 4 1v3c0 1-1 2-2 2C7 15 1 9 1 3c0-1 1-2 2-2z"/></svg>
      <span>01234 567 89 00</span>
    </li>
    <li>
      <svg viewBox="0 0 16 16"><path d="M3 1h3l1 4-2 1a9 9 0 0 0 5 5l1-2 4 1v3c0 1-1 2-2 2C7 15 1 9 1 3c0-1 1-2 2-2z"/></svg>
      <span>01234 567 89 01</span>
    </li>
    <li>
      <svg viewBox="0 0 16 16"><path d="M2 3h12v10H2z M2 3l6 5 6-5" stroke="#fff" stroke-width="1"/></svg>
      <span>hallo@keimlinge-kita.de</span>
    </li>
  </ul>
</section>

</body>
</html>
```